Redesign of LumoWordfind.com in Bootstrap 4

Current design of LumoWordfind.com is not responsive. We need to change it to latest version of Bootstrap 4 keeping essential elements in place.

Apart from home page, we need designs for http://www.lumowordfind.com/meaning/cat also.

Coding

Number of Pages Required

2 page

Colors
34a7d8

Requirements
Must have
• Bootstrap 4

```html
<!DOCTYPE html>
<html lang="en">
<head>
<meta charset="utf-8">
<title>Lumo Wordfind – English Dictionary</title>
<link rel="stylesheet" href="https://fonts.googleapis.com/css2?family=Raleway:wght@400;500;600&family=PT+Sans:ital,wght@0,400;0,700;1,400&display=swap">
<style>
:root{
  --accent:#f39c12;
  --blue:#34a7d8;
  --blue-dark:#1f7fb0;
  --gold:#e0a233;
  --gold-dark:#c8862a;
  --text:#555;
  --muted:#888;
  --line:#e2e2e2;
  --footer:#1c1c1c;
  --page:#f7f7f7;
}
*{box-sizing:border-box;margin:0;padding:0}
html,body{width:935px;height:1200px;overflow:hidden}
body{position:relative;background:var(--page);font-family:"PT Sans",sans-serif;color:var(--text);font-size:11px}
.abs{position:absolute}
.topbar{left:0;top:0;width:935px;height:3px;background:var(--accent)}
.site-header{left:0;top:3px;width:935px;height:91px;background:#fbfbfb;border-bottom:1px solid #e6e6e6}
.brand{left:77px;top:29px;font-family:"PT Sans",sans-serif;font-weight:700;font-size:20px;color:var(--accent);display:flex;align-items:center;gap:6px}
.brand .dot{width:12px;height:12px;border-radius:50%;background:var(--blue)}
.main-nav{left:390px;top:40px;display:flex;gap:25px;font-size:13px;color:#666}
.main-nav .active{color:var(--accent)}
.nav-search{left:846px;top:44px}
.hero{left:0;top:94px;width:935px;height:413px;background:linear-gradient(180deg,#2d6a70 0%,#3f8a8c 35%,#8c7660 70%,#b0703a 100%)}
.hero-mark{left:0;width:935px;top:185px;text-align:center;font-family:"Raleway",sans-serif;font-weight:600;font-size:46px;color:rgba(255,255,255,.85)}
.hero-title{left:0;width:935px;top:258px;text-align:center;font-family:"Raleway",sans-serif;font-weight:600;font-size:26px;color:#fff}
.hero-arrow{top:280px}
.search-field{left:230px;top:312px;width:354px;height:40px;background:#fff;border-radius:2px;padding:12px 21px;font-style:italic;font-size:11px;color:#999}
.search-btn{left:590px;top:312px;width:115px;height:40px;background:var(--gold);color:#fff;font-weight:700;font-size:12px;text-align:center;line-height:40px;border-radius:2px}
.browse-bar{left:77px;top:420px;width:781px;height:40px;background:rgba(255,255,255,.14);display:flex;align-items:center;padding-left:22px}
.browse-bar span{color:#fff;font-size:12px;width:133px}
.letters{display:flex;gap:4.2px}
.letters b{width:19px;height:16px;background:linear-gradient(#f4f4f4,#cfcfcf);border-radius:2px;font-weight:400;font-size:8px;color:#444;text-align:center;line-height:16px}
.section-title{font-family:"Raleway",sans-serif;font-size:17px;color:var(--blue)}
.features{left:77px;top:595px;width:230px;list-style:none;line-height:18px}
.features li{padding-left:24px;position:relative;margin-bottom:7px}
.features li svg{position:absolute;left:0;top:4px}
.col-rule{left:333px;top:555px;width:1px;height:562px;background:var(--line)}
.hrule{height:1px;background:var(--line)}
.wotd{left:91px;top:812px;width:210px;height:113px;background:var(--gold);border-radius:2px;color:#fff;overflow:hidden}
.wotd h3{font-family:"Raleway",sans-serif;font-weight:500;font-size:16px;text-align:center;margin-top:10px}
.wotd .word{text-align:center;font-size:13px;color:#6b4a18;margin-top:6px}
.wotd .phon{position:absolute;left:23px;top:68px;font-size:9px;color:#4a3412;font-style:italic}
.wotd .show{position:absolute;right:16px;top:67px;font-size:10px;text-decoration:underline}
.wotd .foot{position:absolute;left:0;bottom:0;width:100%;height:20px;background:#eab44e;padding:4px 8px}
.email-label{left:77px;top:1016px;font-style:italic;color:#888;font-size:10px}
.email-input{left:77px;top:1038px;width:169px;height:27px;border:1px solid #d6d6d6;background:#fff;border-radius:2px}
.submit-btn{left:77px;top:1074px;width:67px;height:24px;background:linear-gradient(var(--blue),var(--blue-dark));color:#fff;font-weight:700;font-size:10px;text-align:center;line-height:24px;border-radius:2px}
.card-img{width:225px;height:138px;border:1px solid #ddd}
.card-title{font-family:"Raleway",sans-serif;font-size:17px;color:var(--blue)}
.card-sub{font-style:italic;font-size:10px;color:#999}
.card-text{width:215px;font-size:10px;line-height:17.5px}
.learn-btn{left:365px;top:1084px;width:101px;height:32px;background:linear-gradient(var(--blue),var(--blue-dark));color:#fff;font-size:11px;text-align:center;line-height:32px;border-radius:2px}
.site-footer{left:0;top:1144px;width:935px;height:56px;background:var(--footer)}
.copyright{left:77px;top:1164px;color:#ddd;font-size:10px}
.social{left:733px;top:1160px;display:flex;gap:4.5px}
.social i{width:22px;height:22px;border:1.5px solid #ddd;border-radius:50%}
.social i:first-child{border-color:var(--blue)}
</style>
</head>
<body>
<div class="abs topbar"></div>
<header class="abs site-header"></header>
<div class="abs brand"><i class="dot"></i>Lumo Wordfind</div>
<nav class="abs main-nav"><span class="active">Home</span><span>Idioms</span><span>Common Errors</span><span>Crossword</span><span>Blog</span><span>Contact</span></nav>
<svg class="abs nav-search" width="10" height="10" viewBox="0 0 10 10"><circle cx="4" cy="4" r="3" fill="none" stroke="#666" stroke-width="1.5"/><line x1="6.3" y1="6.3" x2="9" y2="9" stroke="#666" stroke-width="1.5"/></svg>

<section class="abs hero" role="img" aria-label="Blurred photo of books, a globe and a magnifying glass on a desk"></section>
<div class="abs hero-mark">Lumo</div>
<h1 class="abs hero-title">Lumo English Dictionary</h1>
<svg class="abs hero-arrow" style="left:27px" width="22" height="42" viewBox="0 0 22 42"><polyline points="20,1 2,21 20,41" fill="none" stroke="rgba(255,255,255,.6)" stroke-width="1.5"/></svg>
<svg class="abs hero-arrow" style="left:880px" width="22" height="42" viewBox="0 0 22 42"><polyline points="2,1 20,21 2,41" fill="none" stroke="rgba(255,255,255,.6)" stroke-width="1.5"/></svg>
<div class="abs search-field">Enter a Word or Phrase ...</div>
<div class="abs search-btn">SEARCH</div>
<div class="abs browse-bar"><span>Browse Dictionary</span>
  <div class="letters"><b>A</b><b>B</b><b>C</b><b>D</b><b>E</b><b>F</b><b>G</b><b>H</b><b>I</b><b>J</b><b>K</b><b>L</b><b>M</b><b>N</b><b>O</b><b>P</b><b>Q</b><b>R</b><b>S</b><b>T</b><b>U</b><b>V</b><b>W</b><b>X</b><b>Y</b><b>Z</b></div>
</div>

<h2 class="abs section-title" style="left:76px;top:551px">Search, Save and Master Words</h2>
<ul class="abs features">
  <li><svg width="10" height="8" viewBox="0 0 10 8"><polyline points="1,4 4,7 9,1" fill="none" stroke="#f39c12" stroke-width="2"/></svg>Search from more than 300,000 words and phrases</li>
  <li><svg width="10" height="8" viewBox="0 0 10 8"><polyline points="1,4 4,7 9,1" fill="none" stroke="#f39c12" stroke-width="2"/></svg>Multiple usages to clarify the context</li>
  <li><svg width="10" height="8" viewBox="0 0 10 8"><polyline points="1,4 4,7 9,1" fill="none" stroke="#f39c12" stroke-width="2"/></svg>Audio, phonetics, meanings, synonyms and antonyms</li>
  <li><svg width="10" height="8" viewBox="0 0 10 8"><polyline points="1,4 4,7 9,1" fill="none" stroke="#f39c12" stroke-width="2"/></svg>Save the words to your personal deck and access from anywhere</li>
  <li><svg width="10" height="8" viewBox="0 0 10 8"><polyline points="1,4 4,7 9,1" fill="none" stroke="#f39c12" stroke-width="2"/></svg>It's FREE</li>
</ul>
<div class="abs hrule" style="left:77px;top:779px;width:256px"></div>
<div class="abs col-rule"></div>

<div class="abs wotd">
  <h3>Word Of the Day</h3>
  <div class="word">exhaustive &#128266;</div>
  <div class="phon">/ɪɡˈzɔːstɪv/</div>
  <div class="show">Show Definitions</div>
  <div class="foot"><svg width="22" height="9" viewBox="0 0 22 9"><circle cx="2" cy="7" r="1.3" fill="#fff"/><path d="M1 3a5 5 0 0 1 5 5M1 0.5a7.5 7.5 0 0 1 7.5 7.5" fill="none" stroke="#fff" stroke-width="1.2"/><path d="M13 6l3 2 5-7" fill="none" stroke="#fff" stroke-width="1.6"/></svg></div>
</div>
<div class="abs hrule" style="left:77px;top:960px;width:256px"></div>

<h2 class="abs section-title" style="left:75px;top:980px">Newsletter Sign Up</h2>
<div class="abs email-label">Enter your email here</div>
<div class="abs email-input"></div>
<div class="abs submit-btn">SUBMIT</div>

<div class="abs card-img" style="left:372px;top:554px;background:linear-gradient(135deg,#3d3d3d,#262626)" role="img" aria-label="Dark graphic comparing the words gaffe and gaff"></div>
<h3 class="abs card-title" style="left:371px;top:704px">English Tidbit</h3>
<div class="abs card-sub" style="left:373px;top:729px">gaffe / gaff</div>
<p class="abs card-text" style="left:369px;top:747px">"Gaffe" is a social blunder and "gaff" is a large hook. Be warned not to make the gaffe of mixing it up with gaff.</p>

<div class="abs card-img" style="left:632px;top:554px;background:linear-gradient(135deg,#d8d4c8,#6e6a60)" role="img" aria-label="Close-up photo of a pen over a crossword puzzle"></div>
<h3 class="abs card-title" style="left:632px;top:704px">Daily Crossword</h3>
<div class="abs card-sub" style="left:633px;top:729px">Crossword Lovers!</div>
<p class="abs card-text" style="left:629px;top:747px">Take this daily crossword challenge from Lumo Wordfind</p>

<div class="abs card-img" style="left:371px;top:819px;background:linear-gradient(135deg,#cdb592,#5d4b34)" role="img" aria-label="Sepia photo of a magnifying glass over a dictionary page"></div>
<h3 class="abs card-title" style="left:370px;top:969px">Kestrel Browser Addon</h3>
<p class="abs card-text" style="left:368px;top:994px">Add this tool to your Kestrel and quickly look up for definitions from any website without leaving the page.</p>

<div class="abs card-img" style="left:632px;top:819px;background:linear-gradient(135deg,#f0f0f0,#d9c4b4)" role="img" aria-label="Photo of a hand holding a smartphone"></div>
<h3 class="abs card-title" style="left:632px;top:969px">Designed for Orbit Phone</h3>
<p class="abs card-text" style="left:631px;top:994px">Lumo Wordfind is specially designed for your Orbit Phone to quickly lookup meaning, usages and audio of words.</p>

<div class="abs hrule" style="left:365px;top:1067px;width:499px"></div>
<div class="abs learn-btn">Learn More &gt;&gt;</div>

<footer class="abs site-footer"></footer>
<div class="abs copyright">Copyright © 2016 lumowordfind.net, All Rights Reserved.</div>
<div class="abs social"><i></i><i></i><i></i><i></i><i></i></div>
</body>
</html>
```